sydney wedding photography business needs a business card design

we need a business card design for a sydney based wedding photography and videography business. our business name is :golden hour studio and film. our target clients are 24-35 yrs female. our style is candid, organic, natural, dynamic. we are a team of young photographers and videographers, and help brides to create memories that they will cherish for the rest of their lives. the logo will be provided. we want an elegant design that reflects our style, and also want to give a great impression to our clients that we are one of the best studios in sydney and our brand means quality and premium service.

Target Market(s)

bride to be, 24-35 years old, living in sydney and surrunding areas

Industry/Entity Type

Wedding Photography

Contact Information for Business Card

address: 57 tarrant street, glenmore nsw 2047
mobile: 0431872259
phone: (02) 9163 2408
info@tidewillowstudio.net.au
www.tidewillowstudio.net.au
facebook:tidewillowweddings
instagram:tidewillowweddings

Font styles to use
Serif
Sans Serif

Requirements
Nice to have
• maybe add my slogan"memories beyond eternity" if the layout looks good
Should not have
• no black color, not good idea for wedding biz card

```html
<!DOCTYPE html>
<html lang="en">
<head>
<meta charset="utf-8">
<title>Golden Hour Studio and Film – Business Card</title>
<link rel="stylesheet" href="https://fonts.googleapis.com/css2?family=Open+Sans:wght@400;600&display=swap">
<style>
  :root {
    --stage: #000000;
    --paper: #f3f3f3;
    --gold: #d9a21b;
    --gold-deep: #ad7719;
    --gold-bright: #f6c500;
    --ink: #1e1e1e;
    --white: #ffffff;
  }
  * { margin: 0; padding: 0; box-sizing: border-box; }
  html, body { width: 1200px; height: 900px; overflow: hidden; }
  body {
    background: var(--stage);
    font-family: "Open Sans", Arial, sans-serif;
    position: relative;
  }
  .card {
    position: absolute;
    top: 200px;
    width: 310px;
    height: 502px;
  }
  .card--front {
    left: 265px;
    background: var(--paper);
    border-radius: 62px 0 62px 0;
  }
  .card--back {
    left: 641px;
    width: 309px;
    background: linear-gradient(180deg, var(--gold-deep) 0%, #c99214 45%, var(--gold-bright) 100%);
    border-radius: 0 62px 0 62px;
  }
  .wordmark {
    position: absolute;
    left: 0;
    width: 100%;
    text-align: center;
    font-weight: 600;
    line-height: 1;
  }
  .wordmark__name { display: block; font-size: 30px; letter-spacing: 0.5px; }
  .wordmark__line { display: block; font-size: 11px; letter-spacing: 5px; margin-top: 8px; }
  .card--front .wordmark { top: 66px; color: var(--gold); }
  .card--back .wordmark { top: 386px; color: var(--white); }

  .person { position: absolute; left: 28px; top: 291px; }
  .person__name { font-size: 16px; font-weight: 600; color: var(--gold); line-height: 20px; }
  .person__role { font-size: 13px; color: var(--ink); line-height: 18px; }

  .address { position: absolute; left: 28px; top: 341px; font-size: 13px; line-height: 18px; color: var(--ink); font-style: normal; }

  .contacts { position: absolute; left: 28px; top: 390px; list-style: none; }
  .contacts li { display: flex; align-items: center; height: 18px; font-size: 13px; color: var(--ink); }
  .contacts svg { width: 10px; height: 10px; margin-right: 8px; fill: var(--gold); }

  .social { position: absolute; left: 33px; top: 457px; display: flex; gap: 13px; }
  .social span { width: 22px; height: 22px; border-radius: 50%; background: var(--gold); display: block; }
</style>
</head>
<body>
  <section class="card card--front" aria-label="Business card front">
    <div class="wordmark">
      <span class="wordmark__name">Golden Hour</span>
      <span class="wordmark__line">STUDIO AND FILM</span>
    </div>

    <div class="person">
      <p class="person__name">Daniel Rowe</p>
      <p class="person__role">Managing Director</p>
    </div>

    <address class="address">57 Tarrant Street,<br>Glenmore NSW 2047</address>

    <ul class="contacts">
      <li><svg viewBox="0 0 10 10" aria-hidden="true"><path d="M2 0.5 L3.6 2.8 L2.7 3.8 Q4 6 6.2 7.3 L7.2 6.4 L9.5 8 L8.4 9.5 Q3.5 9 0.5 1.6 Z"/></svg>0431 872 259</li>
      <li><svg viewBox="0 0 10 10" aria-hidden="true"><path d="M0.5 2 H9.5 V8 H0.5 Z M0.5 2 L5 5.5 L9.5 2" stroke="#f3f3f3" stroke-width="0.8"/></svg>info@tidewillowstudio.net.au</li>
      <li><svg viewBox="0 0 10 10" aria-hidden="true"><circle cx="5" cy="5" r="4.6"/><path d="M0.5 5 H9.5 M5 0.5 Q2 5 5 9.5 Q8 5 5 0.5" stroke="#f3f3f3" stroke-width="0.7" fill="none"/></svg>www.tidewillowstudio.net.au</li>
    </ul>

    <div class="social" aria-label="Social media links">
      <span></span><span></span><span></span><span></span>
    </div>
  </section>

  <section class="card card--back" aria-label="Business card back">
    <div class="wordmark">
      <span class="wordmark__name">Golden Hour</span>
      <span class="wordmark__line">STUDIO AND FILM</span>
    </div>
  </section>
</body>
</html>
```